Website Design Required For Education Video Portfolio Site

I am looking for a designer to create a skin for a relaunch of my website - www.brackenlearningfilms.co.uk. We want a clean and stylish new design.

The website showcases prospectus/promotional videos that are made for schools and colleges. Videos will be hosted on YouTube and embedded.

I want it to be stylish and clean.

I require 7 pages designed and this must be agreed in order to do the project.

1. Homepage
2. About
3. Prices
4. Testimonials
5. Contact Page with form
6. Promotional Videos
7. Subject Videos

The website will be then be built on the Wordpress system.

Target Market(s)

Education, Schools, Colleges, Universities

Industry/Entity Type

Education

Font styles to use
Serif

Colors

Designer to choose colors to be used in the design.

Requirements
Must have
• Video content, be clean, show our portfolio, descriptions about videos. I like the idea of having video headers.
Nice to have
• Images

```html
<!DOCTYPE html>
<html lang="en">
<head>
<meta charset="utf-8">
<title>Bracken Learning Films</title>
<link href="https://fonts.googleapis.com/css2?family=Poppins:wght@400;500;600;700;800&family=Open+Sans:wght@400;600;700&display=swap" rel="stylesheet">
<style>
:root{
  --blue:#1ca7e6;
  --blue-light:#5cc3f0;
  --navy:#0d2a3d;
  --ink:#1b1b1b;
  --grey-bg:#f2f2f2;
  --pale-blue:#eaf6fd;
  --red:#e5253a;
  --white:#ffffff;
  --black:#000000;
}
*{box-sizing:border-box;margin:0;padding:0}
html,body{width:1200px;height:5042px;overflow:hidden}
body{position:relative;font-family:"Open Sans",sans-serif;color:var(--ink);background:var(--white)}
.abs{position:absolute}
.heading{font-family:"Poppins",sans-serif;font-weight:600;font-size:34px;color:var(--ink);position:absolute;white-space:nowrap;z-index:1}
.heading::before{content:"";position:absolute;left:-24px;top:-14px;width:66px;height:66px;border-radius:50%;background:var(--blue);z-index:-1}
.heading::after{content:"";position:absolute;right:-22px;top:-14px;width:32px;height:32px;border-radius:50%;background:var(--blue-light);opacity:.9;z-index:-1}
.heading.center{left:50%;transform:translateX(-50%)}

/* header */
.site-header{left:0;top:0;width:1200px;height:84px;background:var(--white)}
.brand{left:113px;top:25px;display:flex;align-items:center;gap:10px;font-family:"Poppins",sans-serif;font-weight:700;font-size:21px;color:var(--blue);white-space:nowrap}
.brand .dot{width:32px;height:32px;border-radius:50%;background:var(--black)}
.main-nav{left:461px;top:30px;display:flex;gap:24px;font-size:13px;color:#444;white-space:nowrap}

/* hero */
.hero{left:0;top:84px;width:1200px;height:509px;background:linear-gradient(180deg,#6d7f5b 0%,#8a9585 35%,#9aa098 60%,#707e5c 100%)}
.hero-shade{left:0;top:0;width:100%;height:100%;background:rgba(20,30,20,.25)}
.hero-text{left:0;width:1200px;text-align:center;color:var(--white);font-family:"Poppins",sans-serif}
.hero .t1{top:178px;font-size:22px;font-weight:400}
.hero .t2{top:214px;font-size:26px;font-weight:400;letter-spacing:1px}
.hero .t3{top:240px;font-size:108px;font-weight:800;letter-spacing:2px}
.play{border-radius:50%;background:var(--white);display:flex;align-items:center;justify-content:center}
.play span{width:0;height:0;border-style:solid;border-color:transparent transparent transparent var(--white)}
.play i{display:flex;align-items:center;justify-content:center;border-radius:50%;background:var(--blue)}

/* about */
.about{left:0;top:593px;width:1200px;height:558px;background:var(--grey-bg)}
.photo{border:3px solid var(--white)}
.about-copy{left:650px;top:185px;width:440px;font-size:14px;line-height:23px;color:#222;text-align:justify}
.about-copy p{margin-bottom:14px}
.btn-outline{left:650px;top:382px;width:124px;height:44px;border:1.5px solid #333;border-radius:6px;font-family:"Poppins",sans-serif;font-weight:600;font-size:15px;display:flex;align-items:center;justify-content:center;gap:8px}

/* cards */
.card{width:316px;height:331px;background:var(--white);box-shadow:0 3px 12px rgba(0,0,0,.18);padding:8px}
.card .media{width:100%;height:100%;border:2px solid #ddd;position:relative}
.card .heart,.card .share{position:absolute;right:12px;width:22px;height:22px;border-radius:50%;background:var(--white);display:flex;align-items:center;justify-content:center}
.card .heart{top:12px}
.card .share{top:42px}
.card .play{position:absolute;left:50%;top:50%;transform:translate(-50%,-50%);width:44px;height:44px}
.card .play i{width:34px;height:34px}
.card .play span{border-width:7px 0 7px 11px;margin-left:3px}
.price-pill{position:absolute;left:92px;bottom:18px;background:var(--white);border-radius:16px;padding:6px 14px;font-size:14px;color:#222;white-space:nowrap}
.card-label{width:316px;text-align:center;font-weight:700;font-size:16px;color:#222;line-height:25px}
.card-label em{font-weight:400;font-style:italic}
.arrow{width:30px;height:30px;border:1.5px solid var(--blue);border-radius:50%;display:flex;align-items:center;justify-content:center}

/* testimonials */
.testimonials{left:0;top:1880px;width:1200px;height:461px;background:linear-gradient(90deg,#1596d4 0%,#1ea9e8 50%,#1592cf 100%)}
.testimonials .heading{color:var(--white)}
.testimonials .heading::before{background:var(--black)}
.testimonials .heading::after{background:var(--navy);right:-12px}
.quote-box{left:411px;top:179px;width:661px;height:192px;background:var(--white);box-shadow:0 4px 14px rgba(0,0,0,.2)}
.quote-box p{position:absolute;left:36px;top:44px;width:590px;font-size:14px;line-height:24px;color:#222}
.quote-box .who{position:absolute;left:0;width:100%;top:150px;text-align:center;font-weight:700;font-size:14px;color:var(--navy)}
.role-tab{left:571px;top:147px;width:554px;height:47px;background:var(--navy);color:var(--white);font-family:"Poppins",sans-serif;font-weight:500;font-size:18px;display:flex;align-items:center;justify-content:center;border:1px solid #fff;white-space:nowrap}

/* connect */
.connect{left:0;top:2341px;width:1200px;height:810px;background:var(--white)}
.intro{left:150px;width:900px;text-align:center;font-size:15px;line-height:24px;color:#222}
.form-box{left:117px;top:285px;width:453px;height:417px;background:var(--white);box-shadow:0 4px 16px rgba(0,0,0,.25);border:6px solid #f3f3f3}
.field{position:absolute;left:32px;font-size:14px;color:#222}
.input{position:absolute;left:120px;width:296px;border:1.5px solid #888;background:var(--white)}
.btn-submit{position:absolute;left:126px;top:315px;width:124px;height:44px;background:var(--blue);border:1.5px solid #0e7fb5;border-radius:6px;color:var(--white);font-weight:700;font-size:16px;display:flex;align-items:center;justify-content:center}
.contact-box{left:593px;top:285px;width:476px;height:417px;background:var(--blue);color:var(--white);font-size:16px}
.contact-box h3{position:absolute;left:50px;top:68px;font-family:"Poppins",sans-serif;font-weight:600;font-size:19px}
.ci{position:absolute;left:58px;display:flex;gap:22px;align-items:flex-start;line-height:28px}
.ci .ic{width:32px;height:32px;border-radius:50%;background:var(--white);display:flex;align-items:center;justify-content:center;flex:none}

/* promo */
.promo{left:0;top:3151px;width:1200px;height:763px;background:linear-gradient(180deg,#f4fbff 0%,var(--pale-blue) 100%)}
.tab{height:61px;display:flex;align-items:center;background:var(--white);box-shadow:0 2px 8px rgba(0,0,0,.08)}
.tab .tab-name{flex:1;text-align:center;font-family:"Poppins",sans-serif;font-weight:600;font-size:16px;color:var(--blue);letter-spacing:.5px}
.tab .tab-ic{width:95px;height:61px;background:var(--blue);display:flex;align-items:center;justify-content:center}

/* subject */
.subject{left:0;top:3914px;width:1200px;height:705px;background:var(--white)}

/* footer */
.site-footer{left:0;top:4619px;width:1200px;height:423px;background:var(--black);color:var(--white)}
.partners{left:209px;top:4523px;width:781px;height:223px;background:var(--white);box-shadow:0 4px 16px rgba(0,0,0,.25);z-index:2}
.partners h4{position:absolute;left:0;width:100%;top:20px;text-align:center;font-family:"Poppins",sans-serif;font-weight:600;font-size:15px;letter-spacing:.5px;color:#222}
.badge{position:absolute;width:58px;height:58px;border-radius:50%}
.foot-brand{left:113px;top:157px;display:flex;align-items:center;gap:10px;font-family:"Poppins",sans-serif;font-weight:700;font-size:18px;white-space:nowrap}
.foot-brand .dot{width:28px;height:28px;border-radius:50%;background:var(--white)}
.reg{left:420px;top:160px;display:flex;align-items:center;gap:16px;font-family:"Poppins",sans-serif;font-weight:600;font-size:20px;white-space:nowrap}
.reg b{color:var(--blue)}
.fcol{top:224px;font-size:15px;line-height:27px}
.fcol h5{display:flex;align-items:center;gap:14px;font-family:"Poppins",sans-serif;font-weight:600;font-size:16px;margin-bottom:22px}
.copyright{left:0;top:372px;width:1200px;text-align:center;font-size:14px}
</style>
</head>
<body>

<header class="abs site-header">
  <div class="abs brand"><span class="dot"></span>Bracken Learning Films</div>
  <nav class="abs main-nav"><span>Home</span><span>About</span><span>Prices</span><span>Testimonials</span><span>Contact</span><span>Promotional Videos</span><span>Subject Videos</span></nav>
</header>

<section class="abs hero" role="img" aria-label="Aerial video still of a school campus surrounded by trees and playing fields">
  <div class="abs hero-shade"></div>
  <div class="abs play" style="left:570px;top:68px;width:52px;height:52px"><i style="width:42px;height:42px"><span style="border-width:8px 0 8px 13px;margin-left:3px"></span></i></div>
  <div class="abs hero-text t1">We Make</div>
  <div class="abs hero-text t2">AWESOME EDUCATIONAL</div>
  <div class="abs hero-text t3">VIDEOS</div>
  <svg class="abs" style="left:538px;top:440px" width="120" height="70" viewBox="0 0 120 70"><circle cx="30" cy="30" r="26" fill="#fff"/><circle cx="94" cy="42" r="16" fill="#fff"/><rect x="40" y="38" width="50" height="10" rx="5" fill="#fff" transform="rotate(20 65 43)"/></svg>
</section>

<section class="abs about">
  <div class="abs photo" role="img" aria-label="Photo of young pupils sitting together in class" style="left:113px;top:107px;width:204px;height:323px;background:linear-gradient(160deg,#c9a48c,#d9cfc4 50%,#b3756d)"></div>
  <div class="abs photo" role="img" aria-label="Photo of students with backpacks walking in a corridor" style="left:318px;top:140px;width:270px;height:176px;background:linear-gradient(160deg,#8c8076,#d6c7b4 50%,#4e4b4a)"></div>
  <div class="abs photo" role="img" aria-label="Photo of a teacher helping a child at a table" style="left:318px;top:318px;width:210px;height:178px;background:linear-gradient(160deg,#e2d3c0,#c89a7c 55%,#8f7b6b)"></div>
  <h2 class="heading" style="left:651px;top:98px">About Us</h2>
  <div class="abs about-copy">
    <p>If a picture is worth a thousand words, imagine what a video can do.We help schools, colleges and training providers connect and communicate their ideas through videos.</p>
    <p>Hi, I'm Daniel Hartley, Videographer, Content Creator, Filmmaker. Founder of Bracken Learning Films and dad of two. Thanks for stopping by.</p>
  </div>
  <div class="abs btn-outline">Read More <svg width="22" height="12" viewBox="0 0 22 12"><path d="M0 6h20M15 1l5 5-5 5" stroke="#333" stroke-width="1.6" fill="none"/></svg></div>
</section>

<section class="abs" style="left:0;top:1151px;width:1200px;height:729px">
  <h2 class="heading center" style="top:94px">Price Guide</h2>
  <p class="abs intro" style="top:177px">Offering affordable video content to schools, colleges and training providers in the North of England.</p>
  <div class="abs arrow" style="left:49px;top:378px"><svg width="14" height="10" viewBox="0 0 14 10"><path d="M14 5H2M6 1L2 5l4 4" stroke="#1ca7e6" stroke-width="1.5" fill="none"/></svg></div>
  <div class="abs arrow" style="left:1120px;top:378px"><svg width="14" height="10" viewBox="0 0 14 10"><path d="M0 5h12M8 1l4 4-4 4" stroke="#1ca7e6" stroke-width="1.5" fill="none"/></svg></div>

  <div class="abs card" style="left:110px;top:240px"><div class="media" role="img" aria-label="Photo of a teacher with pupils using a laptop" style="background:linear-gradient(160deg,#dfe4e6,#b8a79a 50%,#7a5d55)">
    <span class="heart"><svg width="12" height="11" viewBox="0 0 12 11"><path d="M6 10.5L1 5.5A3 3 0 016 1.5a3 3 0 015 4z" fill="#e5253a"/></svg></span>
    <span class="share"><svg width="12" height="12" viewBox="0 0 12 12"><circle cx="9" cy="2.5" r="1.8" fill="#1ca7e6"/><circle cx="3" cy="6" r="1.8" fill="#1ca7e6"/><circle cx="9" cy="9.5" r="1.8" fill="#1ca7e6"/><path d="M9 2.5L3 6l6 3.5" stroke="#1ca7e6" fill="none"/></svg></span>
    <div class="play"><i><span></span></i></div>
    <div class="price-pill">start at £1,200</div></div></div>
  <div class="abs card" style="left:440px;top:240px"><div class="media" role="img" aria-label="Photo of a smiling schoolgirl" style="background:linear-gradient(160deg,#efe9e2,#c9a28a 50%,#8b6a58)">
    <span class="heart"><svg width="12" height="11" viewBox="0 0 12 11"><path d="M6 10.5L1 5.5A3 3 0 016 1.5a3 3 0 015 4z" fill="#e5253a"/></svg></span>
    <span class="share"><svg width="12" height="12" viewBox="0 0 12 12"><circle cx="9" cy="2.5" r="1.8" fill="#1ca7e6"/><circle cx="3" cy="6" r="1.8" fill="#1ca7e6"/><circle cx="9" cy="9.5" r="1.8" fill="#1ca7e6"/><path d="M9 2.5L3 6l6 3.5" stroke="#1ca7e6" fill="none"/></svg></span>
    <div class="play"><i><span></span></i></div>
    <div class="price-pill">start at £1,200</div></div></div>
  <div class="abs card" style="left:771px;top:240px"><div class="media" role="img" aria-label="Photo of a music teacher and pupil at a piano" style="background:linear-gradient(160deg,#e6e8ea,#a7988e 50%,#3b3431)">
    <span class="heart"><svg width="12" height="11" viewBox="0 0 12 11"><path d="M6 10.5L1 5.5A3 3 0 016 1.5a3 3 0 015 4z" fill="#e5253a"/></svg></span>
    <span class="share"><svg width="12" height="12" viewBox="0 0 12 12"><circle cx="9" cy="2.5" r="1.8" fill="#1ca7e6"/><circle cx="3" cy="6" r="1.8" fill="#1ca7e6"/><circle cx="9" cy="9.5" r="1.8" fill="#1ca7e6"/><path d="M9 2.5L3 6l6 3.5" stroke="#1ca7e6" fill="none"/></svg></span>
    <div class="play"><i><span></span></i></div>
    <div class="price-pill">start at £1,200</div></div></div>

  <div class="abs card-label" style="left:110px;top:597px">Subject Videos</div>
  <div class="abs card-label" style="left:440px;top:597px">Prospectus Videos<br><em>(Interview based)</em></div>
  <div class="abs card-label" style="left:771px;top:597px">Promotional Videos<br><em>(Music based)</em></div>
</section>

<section class="abs testimonials">
  <h2 class="heading" style="left:162px;top:68px">Testimonials</h2>
  <div class="abs arrow" style="left:49px;top:254px;border-color:#fff"><svg width="14" height="10" viewBox="0 0 14 10"><path d="M14 5H2M6 1L2 5l4 4" stroke="#fff" stroke-width="1.5" fill="none"/></svg></div>
  <div class="abs arrow" style="left:1120px;top:254px;border-color:#fff"><svg width="14" height="10" viewBox="0 0 14 10"><path d="M0 5h12M8 1l4 4-4 4" stroke="#fff" stroke-width="1.5" fill="none"/></svg></div>
  <div class="abs quote-box">
    <p>I just wanted to say a huge thank you for our fabulous Christmas film. It is relaxed and organic and totally captures the spirit or the school. I love the fact it is all about the children. I can't wait to share it with the parent. Thanks again and we will definitely keep you in mind for future events and recommend you to other schools.</p>
    <div class="who">LAURA BENTON</div>
  </div>
  <div class="abs role-tab">Head Teacher, Ashdale Primary School, Millbrook</div>
  <div class="abs" style="left:176px;top:160px;width:70px;height:70px;border-radius:50%;background:#fff"></div>
  <div class="abs" style="left:198px;top:164px;width:226px;height:226px;border-radius:50%;background:var(--blue);border:6px solid #fff"></div>
  <div class="abs" role="img" aria-label="Portrait of a smiling teacher holding a laptop" style="left:214px;top:180px;width:194px;height:194px;border-radius:50%;background:linear-gradient(160deg,#e9ecef,#b8aaa0 55%,#3b3f45)"></div>
  <div class="abs" style="left:374px;top:195px;width:40px;height:40px;border-radius:50%;background:var(--navy)"></div>
</section>

<section class="abs connect">
  <div class="abs" role="img" aria-label="Illustration of a pencil writing on paper" style="left:959px;top:7px;width:241px;height:150px;background:linear-gradient(200deg,#f4f4f4 0%,#ffffff 70%)"></div>
  <h2 class="heading center" style="top:98px">Let’s Connect</h2>
  <p class="abs intro" style="top:187px">We love to listen and hear about your school or college.&nbsp; Please get in touch with us if you have any queries and we will get back to you as soon as possible.</p>
  <div class="abs form-box">
    <span class="field" style="top:71px">Name</span><span class="input" style="top:64px;height:40px"></span>
    <span class="field" style="top:139px">E - Mail</span><span class="input" style="top:134px;height:40px"></span>
    <span class="field" style="top:210px">Message</span><span class="input" style="top:202px;height:76px"></span>
    <span class="btn-submit">Submit</span>
  </div>
  <div class="abs contact-box">
    <h3>Contact Details</h3>
    <div class="ci" style="top:135px"><span class="ic"><svg width="14" height="18" viewBox="0 0 14 18"><path d="M7 17S1 10 1 6.5a6 6 0 0112 0C13 10 7 17 7 17z" fill="#1ca7e6"/><circle cx="7" cy="6.5" r="2.2" fill="#fff"/></svg></span><span>Studio 4,<br>Kestrel Business Park,<br>Hollinby,<br>Northshire - NE0 4QX.</span></div>
    <div class="ci" style="top:275px"><span class="ic"><svg width="16" height="16" viewBox="0 0 16 16"><path d="M3 1l3 3-2 2c1 2 3 4 6 6l2-2 3 3-2 2C7 15 1 9 1 3z" fill="#1ca7e6"/></svg></span><span>07700 900 312</span></div>
    <div class="ci" style="top:328px"><span class="ic"><svg width="16" height="12" viewBox="0 0 16 12"><rect x="1" y="1" width="14" height="10" rx="1" fill="none" stroke="#1ca7e6" stroke-width="1.5"/><path d="M1 1l7 6 7-6" fill="none" stroke="#1ca7e6" stroke-width="1.5"/></svg></span><span>info@brackenlearningfilms.co.uk</span></div>
  </div>
</section>

<section class="abs promo">
  <h2 class="heading center" style="top:72px">Promotional Videos</h2>
  <div class="abs tab" style="left:112px;top:170px;width:487px"><span class="tab-name">SCHOOL &amp; COLLEGE VIDEOS</span><span class="tab-ic"><svg width="34" height="30" viewBox="0 0 34 30"><rect x="2" y="2" width="30" height="26" fill="none" stroke="#fff" stroke-width="2"/><path d="M13 9v12l10-6z" fill="none" stroke="#fff" stroke-width="2"/></svg></span></div>
  <div class="abs tab" style="left:603px;top:170px;width:485px"><span class="tab-name">MULTI VIDEO PACKAGES</span><span class="tab-ic"><svg width="34" height="30" viewBox="0 0 34 30"><rect x="6" y="2" width="26" height="22" fill="none" stroke="#fff" stroke-width="2"/><path d="M2 7v21h26" fill="none" stroke="#fff" stroke-width="2"/><path d="M15 8v10l8-5z" fill="none" stroke="#fff" stroke-width="2"/></svg></span></div>
  <div class="abs arrow" style="left:49px;top:465px"><svg width="14" height="10" viewBox="0 0 14 10"><path d="M14 5H2M6 1L2 5l4 4" stroke="#1ca7e6" stroke-width="1.5" fill="none"/></svg></div>
  <div class="abs arrow" style="left:1120px;top:465px"><svg width="14" height="10" viewBox="0 0 14 10"><path d="M0 5h12M8 1l4 4-4 4" stroke="#1ca7e6" stroke-width="1.5" fill="none"/></svg></div>

  <div class="abs card" style="left:110px;top:289px;height:327px"><div class="media" role="img" aria-label="Video still of children running across a grassy field" style="background:linear-gradient(180deg,#8a9a74,#6f8a4e 55%,#7c9357)">
    <span class="heart"><svg width="12" height="11" viewBox="0 0 12 11"><path d="M6 10.5L1 5.5A3 3 0 016 1.5a3 3 0 015 4z" fill="#e5253a"/></svg></span>
    <span class="share"><svg width="12" height="12" viewBox="0 0 12 12"><circle cx="9" cy="2.5" r="1.8" fill="#1ca7e6"/><circle cx="3" cy="6" r="1.8" fill="#1ca7e6"/><circle cx="9" cy="9.5" r="1.8" fill="#1ca7e6"/><path d="M9 2.5L3 6l6 3.5" stroke="#1ca7e6" fill="none"/></svg></span>
    <div class="play"><i><span></span></i></div></div></div>
  <div class="abs card" style="left:440px;top:289px;height:327px"><div class="media" role="img" aria-label="Video still of a girl concentrating on classwork" style="background:linear-gradient(160deg,#6c6f78,#a38f83 50%,#d7d3d0)">
    <span class="heart"><svg width="12" height="11" viewBox="0 0 12 11"><path d="M6 10.5L1 5.5A3 3 0 016 1.5a3 3 0 015 4z" fill="#e5253a"/></svg></span>
    <span class="share"><svg width="12" height="12" viewBox="0 0 12 12"><circle cx="9" cy="2.5" r="1.8" fill="#1ca7e6"/><circle cx="3" cy="6" r="1.8" fill="#1ca7e6"/><circle cx="9" cy="9.5" r="1.8" fill="#1ca7e6"/><path d="M9 2.5L3 6l6 3.5" stroke="#1ca7e6" fill="none"/></svg></span>
    <div class="play"><i><span></span></i></div></div></div>
  <div class="abs card" style="left:771px;top:289px;height:327px"><div class="media" role="img" aria-label="Video still of young children climbing on a log outdoors" style="background:linear-gradient(180deg,#5f7a45,#3f4a3a 55%,#2f3030)">
    <span class="heart"><svg width="12" height="11" viewBox="0 0 12 11"><path d="M6 10.5L1 5.5A3 3 0 016 1.5a3 3 0 015 4z" fill="#e5253a"/></svg></span>
    <span class="share"><svg width="12" height="12" viewBox="0 0 12 12"><circle cx="9" cy="2.5" r="1.8" fill="#1ca7e6"/><circle cx="3" cy="6" r="1.8" fill="#1ca7e6"/><circle cx="9" cy="9.5" r="1.8" fill="#1ca7e6"/><path d="M9 2.5L3 6l6 3.5" stroke="#1ca7e6" fill="none"/></svg></span>
    <div class="play"><i><span></span></i></div></div></div>

  <div class="abs card-label" style="left:114px;top:643px">Fernside Primary School</div>
  <div class="abs card-label" style="left:444px;top:643px">Oakridge Village Primary<br>School</div>
  <div class="abs card-label" style="left:775px;top:643px">Oakridge Village Primary School</div>
</section>

<section class="abs subject">
  <h2 class="heading center" style="top:62px">Subject Videos</h2>
  <div class="abs arrow" style="left:49px;top:303px"><svg width="14" height="10" viewBox="0 0 14 10"><path d="M14 5H2M6 1L2 5l4 4" stroke="#1ca7e6" stroke-width="1.5" fill="none"/></svg></div>
  <div class="abs arrow" style="left:1120px;top:303px"><svg width="14" height="10" viewBox="0 0 14 10"><path d="M0 5h12M8 1l4 4-4 4" stroke="#1ca7e6" stroke-width="1.5" fill="none"/></svg></div>

  <div class="abs card" style="left:110px;top:153px;height:330px"><div class="media" role="img" aria-label="Video still of a teacher standing by a whiteboard" style="background:linear-gradient(160deg,#7a5a3c,#3b3633 50%,#d9d4cb)">
    <span class="heart"><svg width="12" height="11" viewBox="0 0 12 11"><path d="M6 10.5L1 5.5A3 3 0 016 1.5a3 3 0 015 4z" fill="#e5253a"/></svg></span>
    <span class="share"><svg width="12" height="12" viewBox="0 0 12 12"><circle cx="9" cy="2.5" r="1.8" fill="#1ca7e6"/><circle cx="3" cy="6" r="1.8" fill="#1ca7e6"/><circle cx="9" cy="9.5" r="1.8" fill="#1ca7e6"/><path d="M9 2.5L3 6l6 3.5" stroke="#1ca7e6" fill="none"/></svg></span>
    <div class="play"><i><span></span></i></div></div></div>
  <div class="abs card" style="left:440px;top:153px;height:330px"><div class="media" role="img" aria-label="Video still of a young pupil doing a science activity" style="background:linear-gradient(160deg,#6d4a3c,#1f8a6e 50%,#c84a7a)">
    <span class="heart"><svg width="12" height="11" viewBox="0 0 12 11"><path d="M6 10.5L1 5.5A3 3 0 016 1.5a3 3 0 015 4z" fill="#e5253a"/></svg></span>
    <span class="share"><svg width="12" height="12" viewBox="0 0 12 12"><circle cx="9" cy="2.5" r="1.8" fill="#1ca7e6"/><circle cx="3" cy="6" r="1.8" fill="#1ca7e6"/><circle cx="9" cy="9.5" r="1.8" fill="#1ca7e6"/><path d="M9 2.5L3 6l6 3.5" stroke="#1ca7e6" fill="none"/></svg></span>
    <div class="play"><i><span></span></i></div></div></div>
  <div class="abs card" style="left:771px;top:153px;height:330px"><div class="media" role="img" aria-label="Video still of a pupil working with counting sticks" style="background:linear-gradient(160deg,#3a3634,#7a5e4c 50%,#1f6e4a)">
    <span class="heart"><svg width="12" height="11" viewBox="0 0 12 11"><path d="M6 10.5L1 5.5A3 3 0 016 1.5a3 3 0 015 4z" fill="#e5253a"/></svg></span>
    <span class="share"><svg width="12" height="12" viewBox="0 0 12 12"><circle cx="9" cy="2.5" r="1.8" fill="#1ca7e6"/><circle cx="3" cy="6" r="1.8" fill="#1ca7e6"/><circle cx="9" cy="9.5" r="1.8" fill="#1ca7e6"/><path d="M9 2.5L3 6l6 3.5" stroke="#1ca7e6" fill="none"/></svg></span>
    <div class="play"><i><span></span></i></div></div></div>

  <div class="abs card-label" style="left:114px;top:511px">Geography</div>
  <div class="abs card-label" style="left:444px;top:511px">Science</div>
  <div class="abs card-label" style="left:775px;top:511px">Maths</div>
</section>

<div class="abs partners">
  <h4>SCHOOLS, COLLEGES AND TRAINING PROVIDERS WE'VE WORKED WITH</h4>
  <span class="badge" style="left:103px;top:54px;background:#e7e9f2"></span>
  <span class="badge" style="left:221px;top:54px;background:#d8ecc9"></span>
  <span class="badge" style="left:338px;top:54px;background:#f1efe6"></span>
  <span class="badge" style="left:455px;top:54px;background:#cfe7d5"></span>
  <span class="badge" style="left:590px;top:66px;width:60px;height:34px;border-radius:3px;background:#b7397a"></span>
  <span class="badge" style="left:124px;top:145px;background:#cde9e2"></span>
  <span class="badge" style="left:240px;top:145px;background:#f2d8c6"></span>
  <span class="badge" style="left:358px;top:145px;background:#f4eec5"></span>
  <span class="badge" style="left:474px;top:145px;background:#dbe7f6"></span>
  <span class="badge" style="left:591px;top:145px;background:#2a5aa8"></span>
</div>

<footer class="abs site-footer">
  <div class="abs foot-brand"><span class="dot"></span>Bracken Learning Films</div>
  <div class="abs reg"><svg width="22" height="30" viewBox="0 0 22 30"><circle cx="11" cy="10" r="8" fill="none" stroke="#fff" stroke-width="2"/><path d="M6 16l-2 12 7-4 7 4-2-12" fill="none" stroke="#fff" stroke-width="2"/></svg><span>Company Registration Number: <b>10482736.</b></span></div>
  <div class="abs fcol" style="left:113px;width:250px"><h5><svg width="22" height="22" viewBox="0 0 22 22"><circle cx="11" cy="11" r="9" fill="none" stroke="#fff" stroke-width="2"/><circle cx="11" cy="11" r="4" fill="#fff"/></svg>OUR MISSION</h5>Striving to deliver quality video content for schools and colleges in the North of England.</div>
  <div class="abs fcol" style="left:440px;width:330px"><h5><svg width="22" height="20" viewBox="0 0 22 20"><rect x="1" y="3" width="20" height="14" rx="1" fill="none" stroke="#fff" stroke-width="2"/><path d="M1 3l10 8 10-8" fill="none" stroke="#fff" stroke-width="2"/></svg>CONTACT US</h5>07700 900 312<br><span style="display:block;margin-top:6px">info@brackenlearningfilms.co.uk</span></div>
  <div class="abs fcol" style="left:873px;width:210px"><h5><svg width="22" height="20" viewBox="0 0 22 20"><path d="M2 9l9-7 9 7v9H2z" fill="none" stroke="#fff" stroke-width="2"/></svg>VISIT</h5>Studio 4, Kestrel Business Park, Hollinby, Northshire. NE0 4QX.</div>
  <div class="abs copyright">© Bracken Learning Films Limited 2022. All Rights Reserved</div>
</footer>

</body>
</html>
```